Corvy

Electronic Repairs for OEM's Industrial electronic repairs, consumer audio visual, Projectors

Target Market(s)

manufacturer of electronics (OEM), business, Government, then Consumer

Industry/Entity Type

Electronic Repair

Contact Information for Business Card

Board Repair, Projectors

Font styles to use
Serif

Colors
0054AA
0677BA
7BADD7
CADEEF
E8F1F8

Requirements
Must have
• projector, led wall image
Nice to have
• professional looking business card.
Should not have
• unsure

```html
<!DOCTYPE html>
<html lang="en">
<head>
<meta charset="utf-8">
<title>Corvy Electronic Repairs – Business Card</title>
<link href="https://fonts.googleapis.com/css2?family=Oswald:wght@500;600&family=Roboto+Condensed:ital,wght@0,400;1,400;1,700&display=swap" rel="stylesheet">
<style>
  :root {
    --blue-deep: #0054AA;
    --blue-mid: #0677BA;
    --blue-soft: #7BADD7;
    --blue-pale: #CADEEF;
    --blue-mist: #E8F1F8;
    --ink: #1a1a1a;
    --white: #ffffff;
    --page: #e4e6ea;
  }
  * { margin: 0; padding: 0; box-sizing: border-box; }
  html, body {
    width: 1200px; height: 969px; overflow: hidden;
    background: var(--page);
  }
  .card {
    position: absolute; left: 50px; top: 172px;
    width: 1100px; height: 625px;
    border-radius: 32px; overflow: hidden;
    background: var(--white);
    box-shadow: 0 10px 30px rgba(0,0,0,.18);
  }
  .card__wave { position: absolute; left: 0; top: 0; width: 1100px; height: 625px; }
  .brand {
    position: absolute; left: 0; right: 0; top: 42px;
    text-align: center; white-space: nowrap;
    font-family: "Oswald", sans-serif; font-weight: 600;
    font-size: 94px; line-height: 1; letter-spacing: -0.5px;
    color: var(--white);
    transform: scaleX(0.84); transform-origin: center top;
  }
  .tagline {
    position: absolute; left: 0; right: 0; top: 147px;
    text-align: center; white-space: nowrap;
    font-family: "Roboto Condensed", sans-serif; font-style: italic;
    font-size: 25px; line-height: 1.2; color: var(--white); letter-spacing: .2px;
  }
  .tagline strong { font-weight: 700; }
  .service {
    position: absolute; top: 197px; width: 272px;
    display: flex; flex-direction: column; align-items: center;
  }
  .service__photo {
    width: 272px; height: 272px; border-radius: 50%;
    border: 7px solid var(--white);
    box-shadow: 0 4px 12px rgba(0,0,0,.25);
  }
  .service__photo--projector { background: radial-gradient(circle at 35% 50%, #6aa6c0 0%, #2f6f8f 40%, #143a52 100%); }
  .service__photo--ledwall { background: linear-gradient(180deg, var(--blue-pale), #bcd6ef); }
  .service__photo--board { background: radial-gradient(circle at 55% 45%, #9cc4e6 0%, #2f6fb3 45%, #123f7a 100%); }
  .service__label {
    margin-top: 12px;
    font-family: "Oswald", sans-serif; font-weight: 500;
    font-size: 31px; line-height: 1; color: var(--ink);
    white-space: nowrap;
  }
  .service--projector { left: 99px; }
  .service--ledwall { left: 397px; }
  .service--board { left: 696px; }
  .contact {
    position: absolute; left: 0; right: 0; top: 558px;
    text-align: center;
    font-family: "Roboto Condensed", sans-serif; font-size: 35px; line-height: 1;
    white-space: nowrap;
  }
  .contact__label { color: var(--blue-mid); }
  .contact__value { color: var(--ink); }
  .contact__phone { font-family: "Oswald", sans-serif; font-weight: 500; margin-right: 26px; }
  .contact__email { font-style: italic; }
</style>
</head>
<body>
  <div class="card">
    <svg class="card__wave" viewBox="0 0 1100 625" aria-hidden="true">
      <defs>
        <linearGradient id="bandBlue" x1="0" y1="0" x2="0" y2="1">
          <stop offset="0" stop-color="#0054AA"/>
          <stop offset="1" stop-color="#0677BA"/>
        </linearGradient>
      </defs>
      <path d="M0 0 H1100 V300 C980 285 860 300 760 330 C640 365 560 360 470 345 C330 320 160 300 0 312 Z" fill="url(#bandBlue)"/>
    </svg>

    <h1 class="brand">CORVY ELECTRONIC REPAIRS</h1>
    <p class="tagline">Electronic Repairs for <strong>OEM's Industrial electronic repairs, consumer audio visual, Projectors</strong></p>

    <div class="service service--projector">
      <div class="service__photo service__photo--projector" role="img" aria-label="Photo of a technician servicing a ceiling-mounted projector"></div>
      <span class="service__label">PROJECTOR</span>
    </div>
    <div class="service service--ledwall">
      <div class="service__photo service__photo--ledwall" role="img" aria-label="Image of an LED wall display panel frame"></div>
      <span class="service__label">LED WALL IMAGE</span>
    </div>
    <div class="service service--board">
      <div class="service__photo service__photo--board" role="img" aria-label="Close-up photo of a circuit board being repaired"></div>
      <span class="service__label">BOARD REPAIR</span>
    </div>

    <p class="contact">
      <span class="contact__label">CALL US</span>
      <span class="contact__value contact__phone">123-456-7890</span>
      <span class="contact__label">EMAIL US</span>
      <span class="contact__value contact__email">info@corvyelectronicrepairs.com</span>
    </p>
  </div>
</body>
</html>
```